Vantoq Business Card Project showing the logo and a marbo image on the rear

Design a whacky but professional business card, the logo is for the front and the Marbo image is for the rear. Happy to consider other open source Marbo Images if the designer wants to select one from the web. Vantoq is a competitor to OMB.com.au and Pellory.com.au and is based around every property in Australia

Target Market(s)

Business

Contact Information for Business Card

Name, Title, Email, Web, Phone Number

Font styles to use
Other font styles liked:
• avenir

Requirements
Must have
• Image on Back logo on front
Nice to have
• Happy to consider other images on rear, preftably Colin Marbo. Image supplied I own, we can use open source other Marbo Images

```html
<!DOCTYPE html>
<html lang="en">
<head>
<meta charset="utf-8">
<title>Vantoq Business Card</title>
<link rel="stylesheet" href="https://fonts.googleapis.com/css2?family=Poppins:wght@400;500;600&display=swap">
<style>
  :root {
    --backdrop: #1e1e1e;
    --card: #f1f1f0;
    --ink: #141414;
    --accent: #f08a0c;
    --city-a: #e8348a;
    --city-b: #3fa0d8;
    --city-c: #a3d23c;
    --city-d: #f0703a;
    --city-e: #f5d63a;
    --ground: #7cc242;
  }
  * { margin: 0; padding: 0; box-sizing: border-box; }
  html, body { width: 1200px; height: 1138px; overflow: hidden; }
  body {
    background: var(--backdrop);
    font-family: "Poppins", sans-serif;
    color: var(--ink);
    position: relative;
  }
  .card {
    position: absolute;
    background: var(--card);
    border-radius: 13px;
    overflow: hidden;
    box-shadow: 0 6px 18px rgba(0,0,0,.45);
  }
  .card--front { left: 274px; top: 186px; width: 622px; height: 376px; }
  .card--back  { left: 276px; top: 607px; width: 618px; height: 375px; }

  .brand {
    position: absolute;
    display: flex;
    align-items: center;
    font-weight: 600;
    color: var(--ink);
    line-height: 1;
  }
  .brand__mark { background: var(--accent); border-radius: 4px; }
  .card--front .brand { left: 0; right: 0; top: 62px; justify-content: center; gap: 22px; font-size: 64px; }
  .card--front .brand__mark { width: 60px; height: 60px; }
  .card--back .brand { left: 38px; top: 52px; gap: 20px; font-size: 56px; }
  .card--back .brand__mark { width: 52px; height: 52px; }

  .site-line {
    position: absolute;
    left: 0; right: 0; top: 138px;
    text-align: center;
    font-size: 14px;
    letter-spacing: 9px;
    font-weight: 500;
  }

  .cityscape {
    position: absolute;
    left: 0; right: 0; bottom: 0;
    background:
      linear-gradient(to bottom, transparent 82%, var(--ground) 82%),
      linear-gradient(90deg, var(--city-b), var(--city-a) 14%, var(--city-c) 28%, var(--city-d) 42%, var(--city-a) 56%, var(--city-b) 68%, var(--city-c) 80%, var(--city-a) 90%, var(--city-e));
  }
  .card--front .cityscape { top: 198px; }
  .card--back .cityscape { top: 273px; }

  .person { position: absolute; left: 38px; top: 194px; }
  .person__name { color: var(--accent); font-weight: 600; font-size: 22px; line-height: 1.2; }
  .person__title { font-size: 16px; line-height: 1.5; }

  .contacts { position: absolute; left: 366px; top: 171px; list-style: none; }
  .contacts li { display: flex; align-items: center; gap: 14px; font-size: 16px; height: 24px; }
  .contacts svg { width: 15px; height: 15px; fill: var(--accent); flex: none; }
</style>
</head>
<body>
  <section class="card card--front">
    <div class="brand"><span class="brand__mark"></span><span class="brand__name">Vantoq</span></div>
    <p class="site-line">www.vantoq.com</p>
    <div class="cityscape" role="img" aria-label="Colourful hand-drawn cartoon city of buildings with a tram line along the bottom"></div>
  </section>

  <section class="card card--back">
    <div class="brand"><span class="brand__mark"></span><span class="brand__name">Vantoq</span></div>
    <div class="person">
      <p class="person__name">Tom Keller</p>
      <p class="person__title">Founder &amp; CEO</p>
    </div>
    <ul class="contacts">
      <li><svg viewBox="0 0 16 16" aria-hidden="true"><path d="M2 6c0-2 2-3 6-3s6 1 6 3l-3 1-1-2H6L5 7 2 6zm2 2h8l1 5H3l1-5zm4 1.5a1.5 1.5 0 100 3 1.5 1.5 0 000-3z"/></svg>(00) 4815 2730</li>
      <li><svg viewBox="0 0 16 16" aria-hidden="true"><path d="M1 3h14v10H1zM2 4.5v1L8 9l6-3.5v-1L8 8z" fill-rule="evenodd"/></svg>keller@vantoq.com</li>
      <li><svg viewBox="0 0 16 16" aria-hidden="true"><path d="M8 1a7 7 0 100 14A7 7 0 008 1zm0 1.5c.8 0 1.8 1.9 2 4.8H6c.2-2.9 1.2-4.8 2-4.8zM2.6 7.3C2.9 5 4.5 3.2 6.6 2.6 5.5 3.9 5 5.6 4.9 7.3H2.6zm0 1.4h2.3c.1 1.7.6 3.4 1.7 4.7-2.1-.6-3.7-2.4-4-4.7zM6 8.7h4c-.2 2.9-1.2 4.8-2 4.8s-1.8-1.9-2-4.8zm5.1 0h2.3c-.3 2.3-1.9 4.1-4 4.7 1.1-1.3 1.6-3 1.7-4.7zm0-1.4c-.1-1.7-.6-3.4-1.7-4.7 2.1.6 3.7 2.4 4 4.7h-2.3z"/></svg>www.vantoq.com</li>
    </ul>
    <div class="cityscape" role="img" aria-label="Colourful hand-drawn cartoon city of buildings with a tram line along the bottom"></div>
  </section>
</body>
</html>
```